female esthetician looking for an impact business card

I an an expert in skin care industry with high experience in NYC.I want my business card to look professional , an impact at first look. I do want a combination between white and gold . I believe the font will be great if is gold.. The Fonts are also important. MIRABELA COSTINA (SKIN CARE BOUTIQUE)

THIS SHOULD BE THE BUSINESS NAME, and should be placed on th eback of the card.
IN front m, the name MIRABELA COSTINA - ESTHETCIAN

BY APPOINTMENTS ONLY: 518.240.7136

Target Market(s)

HIGH END CLIENTELE

Contact Information for Business Card

iT WILL BE on a luxury paper. I neeed the wow feeling

Requirements
Should not have
• pictures

```html
<!DOCTYPE html>
<html lang="en">
<head>
<meta charset="utf-8">
<title>Mirabela Costina – Business Card</title>
<link rel="stylesheet" href="https://fonts.googleapis.com/css2?family=Oswald:wght@500&family=Montserrat:wght@400&display=swap">
<style>
  :root {
    --stage: #1c1c1c;
    --paper: #ffffff;
    --gold-deep: #c0902c;
    --gold-mid: #d9b448;
    --gold-light: #f6e784;
    --gold-ink: #c9a13a;
    --white-ink: #ffffff;
  }
  * { box-sizing: border-box; margin: 0; padding: 0; }
  html, body {
    width: 1200px; height: 895px; overflow: hidden;
    background: var(--stage);
  }
  .canvas {
    width: 1200px; height: 895px;
    display: flex; align-items: center; justify-content: center; gap: 40px;
  }
  .card {
    width: 520px; height: 297px; position: relative;
    box-shadow: 0 10px 30px rgba(0,0,0,.5);
  }

  /* Back: gold foil with business name set as plain text */
  .card-back {
    background: linear-gradient(105deg,
      var(--gold-mid) 0%, var(--gold-light) 18%, var(--gold-mid) 34%,
      var(--gold-deep) 48%, var(--gold-light) 66%, var(--gold-mid) 82%, var(--gold-deep) 100%);
    display: flex; flex-direction: column; align-items: center; justify-content: center;
    text-align: center;
  }
  .business-name {
    font-family: "Montserrat", sans-serif; font-weight: 400;
    font-size: 30px; letter-spacing: 3px; line-height: 1.1;
    color: var(--white-ink);
  }
  .business-tagline {
    margin-top: 8px;
    font-family: "Montserrat", sans-serif; font-weight: 400;
    font-size: 13px; letter-spacing: 3px;
    color: var(--white-ink);
  }

  /* Front: white with gold type */
  .card-front { background: var(--paper); }
  .front-frame {
    position: absolute; inset: 18px;
    border: 1.5px solid var(--gold-ink);
    display: flex; flex-direction: column; align-items: center; justify-content: center;
  }
  .person-name {
    font-family: "Oswald", sans-serif; font-weight: 500;
    font-size: 40px; letter-spacing: 2px; line-height: 1;
    color: var(--gold-ink);
  }
  .person-role {
    font-family: "Montserrat", sans-serif; font-size: 13px; letter-spacing: 1.5px;
    color: var(--gold-ink); margin-top: 6px; padding: 0 6px 6px;
    border-bottom: 1.5px solid var(--gold-ink);
  }
  .appointment {
    display: flex; align-items: center; gap: 8px; margin-top: 34px;
    font-family: "Montserrat", sans-serif; font-size: 13px; letter-spacing: 1px;
    color: var(--gold-ink);
  }
  .phone-icon { width: 15px; height: 15px; fill: var(--gold-ink); }
</style>
</head>
<body>
  <main class="canvas">
    <section class="card card-back" aria-label="Card back">
      <p class="business-name">MIRABELA STANCU</p>
      <p class="business-tagline">SKIN CARE BOUTIQUE</p>
    </section>

    <section class="card card-front" aria-label="Card front">
      <div class="front-frame">
        <h1 class="person-name">MIRABELA COSTINA</h1>
        <p class="person-role">ESTHETCIAN</p>
        <p class="appointment">
          BY APPOINTMENTS ONLY:
          <svg class="phone-icon" viewBox="0 0 24 24" aria-hidden="true">
            <path d="M6.6 10.8a15.1 15.1 0 0 0 6.6 6.6l2.2-2.2a1 1 0 0 1 1-.25 11.4 11.4 0 0 0 3.6.57 1 1 0 0 1 1 1V20a1 1 0 0 1-1 1A17 17 0 0 1 3 4a1 1 0 0 1 1-1h3.5a1 1 0 0 1 1 1c0 1.250.2 2.450.57 3.57a1 1 0 0 1-.25 1z"/>
          </svg>
          518.240.7136
        </p>
      </div>
    </section>
  </main>
</body>
</html>
```